Refresh Velquor Web Presence - www.velquor-sample.com

Velquor (www.velquor-sample.com)web site needs a makeover. It needs to be more modern, less cluttered, more corporate, prestigious, user friendly, impressive, up to date. We want a modern corporate image that encourages our business users to trust us and buy our products and services. They need to understand that they are dealing with a highly reputable, long established company, but one that is up to date and forward thinking.
1. Clean uncluttered design.
2. Domain Registration box and Countries (price) box to be collapsible and expandable.
3. All links on page need to be conserved for SEO but hidden from view.
4. Logo and general colour scheme need to be retained.
5. Phone number to be prominently displayed at top of page.
6. No calls to action (CTA) below the fold.
7. Sites we like: www.brinzal-sample.com, www.tundexa-sample.com,www.qop.com,www.plavion-sample.com, www.fismet-sample.com (busy but clear CTAs), www.yarmel-sample.com
Reason: We lost a lot of time to review over the holiday weekend. We need to have a chance to interact during business hours.
Target Market(s)
Small business to large enterprise
Industry/Entity Type
Business
Look and feel

```html
<!DOCTYPE html>
<html lang="en">
<head>
<meta charset="utf-8">
<title>Velquor Corporation — Domain Registration</title>
<link rel="stylesheet" href="https://fonts.googleapis.com/css2?family=Ubuntu:wght@400;500;700&family=PT+Sans+Narrow:wght@700&family=Questrial&display=swap">
<style>
:root{
  --navy:#2d3a8c;
  --orange:#ef7a1f;
  --orange-dark:#d9620e;
  --green:#4fb51c;
  --teal:#8fdcd2;
  --text:#555;
  --line:#dcdcdc;
  --topbar:#333;
  --footer:#3b3b3b;
  --footer-text:#c9c9c9;
  --page:#efefef;
}
*{box-sizing:border-box;margin:0;padding:0}
html,body{width:758px;height:1200px;overflow:hidden}
body{position:relative;background:var(--page);font-family:"Ubuntu",sans-serif;color:var(--text)}
.abs{position:absolute}
a{color:inherit;text-decoration:none}

/* top bar */
.topbar{left:0;top:0;width:758px;height:27px;background:var(--topbar)}
.toplinks{left:84px;top:9px;font-size:7px;color:#ddd;white-space:nowrap}
.toplinks span{margin:0 4px;color:#888}
.toplinks em{font-style:normal;color:var(--orange)}
.social{top:8px;width:11px;height:11px;border-radius:2px}
.whois{left:518px;top:6px;width:102px;height:15px;background:#fff;border-radius:2px;font-size:6.5px;color:#aaa;padding:4px 6px}
.currency{left:632px;top:6px;width:44px;height:15px;background:#fff;border-radius:2px;font-size:6.5px;color:#888;padding:4px 6px}
.currency i{position:absolute;right:0;top:0;width:14px;height:15px;background:#444;border-radius:0 2px 2px 0}

/* header */
.header{left:0;top:27px;width:758px;height:83px;background:#fff}
.brand{left:86px;top:41px;display:flex;align-items:center;gap:6px}
.brand-dot{width:22px;height:22px;border-radius:50%;background:var(--orange)}
.brand-name{font-size:25px;font-weight:700;color:var(--navy);letter-spacing:.5px}
.field{top:47px;height:15px;border:1px solid #ccc;border-radius:2px;font-size:6.5px;color:#aaa;padding:3px 5px;background:#fff}
.login-btn{left:640px;top:47px;width:35px;height:15px;background:#333;color:#fff;font-size:7px;text-align:center;line-height:15px;border-radius:2px}
.forgot{left:615px;top:67px;font-size:6.5px;color:#666}

/* navigation */
.nav{left:82px;top:83px;width:593px;height:27px;background:linear-gradient(#f7923c,var(--orange-dark));display:flex;justify-content:space-around;align-items:center;color:#fff;font-size:8.5px;font-weight:500}

/* hero */
.hero-band{left:0;top:110px;width:758px;height:201px;background:linear-gradient(180deg,#86d9cf,#b9ece4 70%,#e2f6f2)}
.hero-photo{left:82px;top:110px;width:362px;height:201px;background:linear-gradient(100deg,#5f7d8a,#a9c6c4 55%,#c7e6e0)}
.hero-title{left:444px;top:166px;font-family:"Questrial",sans-serif;font-size:32px;line-height:31px;color:#333}
.hero-sub{left:444px;top:231px;font-family:"Questrial",sans-serif;font-size:13.5px;color:#444}
.hero-arrow{top:278px;width:25px;height:25px;border-radius:50%;background:var(--orange)}
.hero-arrow svg{position:absolute;left:7px;top:7px}

/* main container */
.container{left:75px;top:311px;width:607px;height:691px;background:#fff;box-shadow:0 0 4px rgba(0,0,0,.12)}

/* domain search */
.domain-box{left:82px;top:326px;width:593px;height:90px;border:1px solid #ccc;border-radius:2px;background:#f8f8f8}
.domain-title{left:100px;top:334px;font-size:17.5px;font-weight:500;color:var(--navy)}
.domain-links{left:329px;top:340px;font-size:9.5px;color:var(--orange)}
.domain-links span{color:#bbb;margin:0 3px}
.search-field{left:101px;top:362px;width:409px;height:39px;border:1px solid #ccc;border-radius:3px;background:#fff;font-size:11px;color:#888;padding:13px 10px}
.tld{left:361px;top:367px;width:61px;height:29px;background:#666;border-radius:3px;color:#fff;font-size:11px;padding:8px 10px}
.tld svg{position:absolute;right:8px;top:12px}
.search-btn{left:430px;top:366px;width:72px;height:31px;background:linear-gradient(#6bcb2f,var(--green));border:1px solid #3f9a12;border-radius:3px;color:#fff;font-size:12px;text-align:center;line-height:30px}
.tick-item{left:532px;font-size:8px;color:#444;display:flex;align-items:center;gap:8px}

/* about */
.about-title{left:88px;top:460px;font-family:"PT Sans Narrow",sans-serif;font-size:21px;color:var(--navy)}
.vdivider{width:2px;background:linear-gradient(#fff,#ddd,#fff)}
.about-text{left:216px;top:444px;width:446px;font-size:7.8px;line-height:14.4px;color:#555}
.hline{height:1px;background:var(--line)}

/* articles */
.article-logo{left:82px;width:75px;height:68px;border:1px solid #ccc;border-radius:3px;background:#fff}
.article-logo i{position:absolute;left:10px;top:14px;width:53px;height:38px;border-radius:6px}
.article-title{left:170px;font-size:9.5px;color:var(--orange);font-weight:500}
.article-text{left:170px;width:290px;font-size:7.2px;line-height:12.6px;color:#666}
.article-cta{left:170px;font-size:7.3px;color:var(--navy)}
.article-cta u{color:var(--orange)}
.read-more{left:399px;width:63px;height:18px;background:#333;border-radius:3px;color:#fff;font-size:7.5px;font-weight:500;text-align:center;line-height:18px}
.more-domains{left:86px;top:846px;font-size:8.5px;font-weight:500;color:var(--navy);text-decoration:underline}

/* side panels */
.panel{left:486px;width:189px;border:1px solid #ccc;border-radius:3px;background:#f7f7f7}
.ribbon{left:480px;width:126px;height:23px;background:var(--navy);color:#fff;font-size:11.5px;font-weight:500;padding:5px 0 0 17px;clip-path:polygon(0 0,100% 0,94% 100%,0 100%)}
.date-box{left:498px;width:30px;height:31px;border:1px solid #bbb;border-radius:2px;background:#fff;text-align:center;color:var(--navy);font-size:7.5px;line-height:9px;padding-top:3px}
.date-box b{display:block;font-size:11px;line-height:13px;font-weight:500}
.news-title{left:539px;width:130px;font-size:7.2px;line-height:11.5px;color:#555}
.news-more{left:539px;font-size:6.5px;color:var(--orange);font-style:italic}
.read-all{left:594px;top:733px;font-size:8.5px;font-weight:500;color:var(--navy);text-decoration:underline}
.pay-text{left:499px;top:804px;font-size:7.5px;color:#555}
.card{top:822px;width:26px;height:15px;border:1px solid #bbb;border-radius:2px}
.powered{left:500px;top:843px;font-size:5.5px;color:var(--navy)}
.powered b{display:block;font-size:11.5px;font-weight:500}

/* accreditation */
.accr-title{left:88px;top:925px;font-family:"PT Sans Narrow",sans-serif;font-size:21px;color:var(--navy)}
.badge{border-radius:4px}

/* footer */
.footer{left:0;top:1002px;width:758px;height:198px;background:var(--footer)}
.fcol{font-size:7.2px;line-height:14.5px;color:var(--footer-text)}
.fcol h4{font-size:9px;font-weight:500;color:var(--orange);margin-bottom:2px;line-height:14px}
.fdivider{left:82px;top:1112px;width:593px;height:1px;background:#555}
.fbrand{left:466px;top:1132px;display:flex;align-items:center;gap:5px}
.fbrand-dot{width:14px;height:14px;border-radius:50%;background:#ddd}
.fbrand-name{font-size:15px;font-weight:700;color:#fff}
.copy{left:463px;font-size:7.2px;color:var(--footer-text)}
</style>
</head>
<body>

<!-- top bar -->
<div class="abs topbar"></div>
<div class="abs toplinks">Create New Account<span>|</span>Log In<span>|</span>FAQ<span>|</span>Support<span>|</span>Contact Us<span>|</span>View Cart <em>(0)</em></div>
<div class="abs social" style="left:430px;background:#3b5a9a"></div>
<div class="abs social" style="left:446px;background:#3aa0d8"></div>
<div class="abs social" style="left:462px;background:#555"></div>
<div class="abs social" style="left:478px;background:#1a6fa8"></div>
<div class="abs social" style="left:494px;background:#f08a1c"></div>
<div class="abs whois">WHOIS SEARCH
  <svg class="abs" style="right:4px;top:3px" width="9" height="9" viewBox="0 0 9 9"><circle cx="3.5" cy="3.5" r="2.6" fill="none" stroke="#333" stroke-width="1.3"/><line x1="5.5" y1="5.5" x2="8.5" y2="8.5" stroke="#333" stroke-width="1.5"/></svg>
</div>
<div class="abs currency">USD<i><svg width="14" height="15" viewBox="0 0 14 15"><path d="M4 6h6l-3 3z" fill="#fff"/></svg></i></div>

<!-- header -->
<div class="abs header"></div>
<div class="abs brand"><span class="brand-dot"></span><span class="brand-name">velquor</span></div>
<div class="abs field" style="left:428px;width:102px">Username</div>
<div class="abs field" style="left:534px;width:104px">Password</div>
<div class="abs login-btn">Login</div>
<div class="abs forgot">Forgot Password?</div>

<nav class="abs nav">
  <span>HOME</span><span>DOMAIN NAMES</span><span>IDN DOMAINS</span><span>NEW gTLDs</span><span>PHONE NUMBER</span><span>HOSTING</span><span>RESELLERS</span><span>ABOUT US</span>
</nav>

<!-- hero -->
<div class="abs hero-band"></div>
<div class="abs hero-photo" role="img" aria-label="Photo of a smiling business team in suits"></div>
<div class="abs hero-title">Global Brand<br>Protection</div>
<div class="abs hero-sub">Making sure your brand is protected</div>
<div class="abs hero-arrow" style="left:607px"><svg width="11" height="11" viewBox="0 0 11 11"><path d="M7.5 1.5L3.5 5.5l4 4" fill="none" stroke="#5a2a00" stroke-width="2"/></svg></div>
<div class="abs hero-arrow" style="left:641px"><svg width="11" height="11" viewBox="0 0 11 11"><path d="M3.5 1.5l4 4-4 4" fill="none" stroke="#5a2a00" stroke-width="2"/></svg></div>

<!-- main -->
<div class="abs container"></div>

<div class="abs domain-box"></div>
<div class="abs domain-title">Get a Domain Registration</div>
<div class="abs domain-links">IDN<span>|</span>Bulk Search<span>|</span>Transfer<span>|</span>Renew<span>|</span>Map Search<span>|</span>PhNUM</div>
<div class="abs search-field">www.</div>
<div class="abs tld">.com<svg width="9" height="5" viewBox="0 0 9 5"><path d="M0 0h9L4.5 5z" fill="#fff"/></svg></div>
<div class="abs search-btn">SEARCH</div>
<div class="abs tick-item" style="top:367px"><svg width="10" height="9" viewBox="0 0 10 9"><path d="M1 5l3 3 5-7" fill="none" stroke="var(--orange)" stroke-width="2"/></svg>View Price List by Countries</div>
<div class="abs tick-item" style="top:385px"><svg width="10" height="9" viewBox="0 0 10 9"><path d="M1 5l3 3 5-7" fill="none" stroke="var(--orange)" stroke-width="2"/></svg>Bulk Domain&nbsp; Search</div>

<div class="abs about-title">About velquor</div>
<div class="abs vdivider" style="left:203px;top:428px;height:90px"></div>
<p class="abs about-text">Velquor Corporation is one of the world's most experienced and trusted domain name registrars. It holds registry accreditations across the globe including GNRA and countries such as United States, United Kingdom, Germany, Italy, Belgium, Netherlands, Spain, China, Taiwan, Singapore, Australia, New Zealand, Mexico, Brazil and many more.</p>

<div class="abs hline" style="left:82px;top:530px;width:593px"></div>

<!-- article 1 -->
<div class="abs article-logo" style="top:548px"><i style="background:#e9edf5"></i></div>
<div class="abs article-title" style="top:546px">COM.AU - It does what it says on the box.</div>
<p class="abs article-text" style="top:558px">.AUstralia's home on the Internet - COM.AU is trusted by users around the world due to the strict registration policies which maintain the integrity &amp; accuracy of the entire..</p>
<div class="abs article-cta" style="top:604px">Find out if your eligible &amp; <u>Register your .COM.AU today!</u></div>
<div class="abs read-more" style="top:601px">Read More</div>
<div class="abs hline" style="left:82px;top:632px;width:392px"></div>

<!-- article 2 -->
<div class="abs article-logo" style="top:640px"><i style="background:#f3dede"></i></div>
<div class="abs article-title" style="top:639px">CN - Easier Registration Process.</div>
<p class="abs article-text" style="top:651px">Norvelt Registry have recently changed their policy and removed the local presence requirements of the registration process for .CN. In addition, individuals are now eligible to register ..</p>
<div class="abs article-cta" style="top:696px">Find out more &amp; <u>Register your .CN today!</u></div>
<div class="abs read-more" style="top:693px">Read More</div>
<div class="abs hline" style="left:82px;top:722px;width:392px"></div>

<!-- article 3 -->
<div class="abs article-logo" style="top:737px"><i style="background:#f47c20"></i></div>
<div class="abs article-title" style="top:735px">.CO opportunity to express your identity online.</div>
<p class="abs article-text" style="top:747px">With the popularity of extensions like .CO -2012 is the perfect year to express yourself with a unique domain of your own. The internet is changing and the way businesses position themselves in enhancing their brand in the market lead into a strict competition in which identity becomes one of the key factor ..</p>
<div class="abs article-cta" style="top:811px"><u>Create your opportunity with.CO today</u></div>
<div class="abs read-more" style="top:808px">Read More</div>
<div class="abs hline" style="left:82px;top:837px;width:392px"></div>
<div class="abs more-domains">MORE ABOUT DOMAINS</div>
<div class="abs hline" style="left:82px;top:866px;width:593px"></div>

<!-- latest news -->
<div class="abs panel" style="top:538px;height:214px"></div>
<div class="abs ribbon" style="top:549px">Latest News</div>
<svg class="abs" style="left:641px;top:553px" width="30" height="12" viewBox="0 0 30 12"><path d="M6 1L1 6l5 5M24 1l5 5-5 5" fill="none" stroke="#555" stroke-width="1.6"/></svg>

<div class="abs date-box" style="top:582px">Nov<b>23</b></div>
<div class="abs news-title" style="top:580px">Half Million Dollar Sale Tops Charts Second Week In A Row...</div>
<div class="abs news-more" style="top:605px">Read More</div>
<div class="abs hline" style="left:498px;top:622px;width:167px"></div>

<div class="abs date-box" style="top:633px">Nov<b>23</b></div>
<div class="abs news-title" style="top:631px">Velquor Attracts Leading Senior Channel Manager Marta Helvik...</div>
<div class="abs news-more" style="top:656px">Read More</div>
<div class="abs hline" style="left:498px;top:675px;width:167px"></div>

<div class="abs date-box" style="top:686px">Nov<b>22</b></div>
<div class="abs news-title" style="top:684px">GNRA New gTLD Prioritisation Draw Details Announced .....</div>
<div class="abs news-more" style="top:709px">Read More</div>
<div class="abs read-all">READ ALL NEWS</div>

<!-- payment -->
<div class="abs panel" style="top:765px;height:101px"></div>
<div class="abs ribbon" style="top:776px">Payment Mode</div>
<div class="abs pay-text">We accept the following payment methods:</div>
<div class="abs card" style="left:499px;background:#eef1f8"></div>
<div class="abs card" style="left:528px;background:#f6ece2"></div>
<div class="abs card" style="left:557px;background:#e3edf6"></div>
<div class="abs card" style="left:586px;background:#eef1f8"></div>
<div class="abs powered">payments powered by<b>Paylune</b></div>

<!-- accreditation -->
<div class="abs accr-title">Our Accreditation</div>
<svg class="abs" style="left:143px;top:959px" width="30" height="12" viewBox="0 0 30 12"><path d="M6 1L1 6l5 5M24 1l5 5-5 5" fill="none" stroke="#555" stroke-width="1.6"/></svg>
<div class="abs vdivider" style="left:239px;top:893px;height:95px"></div>

<div class="abs badge" style="left:278px;top:898px;width:60px;height:26px;background:#dfe6f0"></div>
<div class="abs badge" style="left:372px;top:893px;width:42px;height:37px;background:#e6ebf2"></div>
<div class="abs badge" style="left:443px;top:898px;width:44px;height:24px;background:#e0eef6"></div>
<div class="abs badge" style="left:518px;top:891px;width:50px;height:38px;background:#f4dede"></div>
<div class="abs badge" style="left:605px;top:895px;width:50px;height:30px;background:#e3e6f2"></div>
<div class="abs badge" style="left:268px;top:948px;width:80px;height:20px;background:#e4ecf4"></div>
<div class="abs badge" style="left:370px;top:941px;width:48px;height:36px;background:#e2e6f4"></div>
<div class="abs badge" style="left:434px;top:942px;width:64px;height:34px;background:#d9d9d9"></div>
<div class="abs badge" style="left:515px;top:946px;width:58px;height:24px;background:#e1e9f4"></div>
<div class="abs badge" style="left:594px;top:940px;width:72px;height:36px;background:#f3e0e0"></div>

<!-- footer -->
<footer class="abs footer"></footer>
<div class="abs fcol" style="left:82px;top:1015px"><h4>Domain Name Registration</h4>Registration<br>Bulk Registration<br>Renewal<br>Transfer<br>Pricing</div>
<div class="abs fcol" style="left:234px;top:1015px"><h4>Domain Name Services</h4>Domain Trustee Services<br>Corporate Domains<br>Company Formation<br>Domain FAQ<br>Map Search</div>
<div class="abs fcol" style="left:386px;top:1015px"><h4>New Top Level Domains</h4>Brand gTLDs<br>Generic gTLDs<br>Geographic gTLDs<br>IDN gTLDs<br>New gTLD Pricing</div>
<div class="abs fcol" style="left:531px;top:1015px"><h4>International Phone Numbers</h4>Global Coverage<br>How It Works<br>PhNUM FAQ<br>Pricing<br>Order</div>
<div class="abs fdivider"></div>
<div class="abs fcol" style="left:82px;top:1124px"><h4>Hosting</h4>Web Hosting Packages<br>Email Hosting Packages<br>Customer Login</div>
<div class="abs fcol" style="left:182px;top:1124px"><h4>Resellers</h4>API Solution<br>Reseller Support<br>Signup</div>
<div class="abs fcol" style="left:266px;top:1124px"><h4>About Velquor</h4>Our Company<br>Our People<br>Our Technology</div>
<div class="abs fcol" style="left:358px;top:1124px"><h4>Quick Support</h4>Domain Support<br>DNS Support<br>Hosting Support</div>
<div class="abs fbrand"><span class="fbrand-dot"></span><span class="fbrand-name">velquor</span></div>
<div class="abs copy" style="top:1156px">Copyright © 1997-2012 Velquor Corporation All Rights Reserved.</div>
<div class="abs copy" style="top:1171px">Privacy Policy | Terms of Services | Sitemap</div>

</body>
</html>
```